Executive recruiting firm in need of business card design

Executive recruiting firm looking for a sleek, classy and modern business card design; card itself will be square shape, rounded edges and soft touch paper, our colors are dark blues in the navy color scale, silvers and grays. Reference our website for a better idea of our company's feel and goals at Tarvex-Up.com - our company message is "Employee Engagement Begins at Recruitment" this should be on the card

```html
<!DOCTYPE html>
<html lang="en">
<head>
<meta charset="utf-8">
<title>Tarvex-Up Business Card</title>
<link rel="stylesheet" href="https://fonts.googleapis.com/css2?family=Roboto:wght@400;500;700&display=swap">
<style>
  :root {
    --backdrop: #b9b9b9;
    --card: #f7f7f7;
    --navy: #15173f;
    --ink: #3f3f44;
    --rule: #55566a;
  }
  * { margin: 0; padding: 0; box-sizing: border-box; }
  html, body { width: 1200px; height: 960px; overflow: hidden; }
  body {
    background: var(--backdrop);
    font-family: "Roboto", Arial, sans-serif;
    position: relative;
  }
  .card {
    position: absolute;
    background: var(--card);
    width: 600px;
    height: 344px;
    left: 320px;
  }
  .card--front { top: 100px; }
  .card--back { top: 493px; }

  .company-name {
    position: absolute;
    left: 0; right: 0;
    text-align: center;
    font-weight: 500;
    color: var(--navy);
    line-height: 1;
  }
  .card--front .company-name { top: 145px; font-size: 40px; }
  .card--back .company-name { top: 76px; font-size: 34px; }

  .slogan {
    position: absolute;
    top: 290px; left: 0; right: 0;
    text-align: center;
    font-size: 14.5px;
    color: var(--ink);
  }

  .divider {
    position: absolute;
    top: 198px; left: 41px;
    width: 517px;
    height: 1px;
    background: var(--rule);
  }
  .divider__accent {
    position: absolute;
    left: 0; top: -3px;
    width: 127px; height: 5px;
    border-radius: 3px;
    background: var(--navy);
  }

  .person {
    position: absolute;
    left: 40px; top: 216px;
    color: var(--ink);
  }
  .person__name {
    font-size: 19px;
    font-weight: 700;
    color: var(--navy);
    text-transform: uppercase;
    line-height: 24px;
  }
  .person__role {
    font-size: 15px;
    font-weight: 400;
    line-height: 22px;
    margin-bottom: 12px;
  }
  .person__address { font-size: 14.5px; line-height: 19px; font-style: normal; }

  .contacts {
    position: absolute;
    right: 42px; top: 216px;
    list-style: none;
    font-size: 14.5px;
    color: var(--ink);
  }
  .contacts li {
    display: flex;
    justify-content: flex-end;
    align-items: center;
    gap: 7px;
    height: 19.3px;
  }
  .contacts svg { width: 13px; height: 13px; fill: var(--navy); flex: none; }
</style>
</head>
<body>

<section class="card card--front">
  <p class="company-name">Tarvex Up</p>
  <p class="slogan">Employee Engagement Begins at Recruitment</p>
</section>

<section class="card card--back">
  <p class="company-name">Tarvex Up</p>

  <div class="divider"><span class="divider__accent"></span></div>

  <div class="person">
    <p class="person__name">Daniel Reyes</p>
    <p class="person__role">CEO/FOUNDER</p>
    <address class="person__address">240 Linden Park Ave.<br>Arcadia, CA</address>
  </div>

  <ul class="contacts">
    <li>612 550 0148
      <svg viewBox="0 0 16 16" aria-hidden="true"><path d="M3.6 1l2.5 3-1.4 1.8c.9 2 2.5 3.6 4.5 4.5L11 8.9l3 2.5-1 3C7 15 1 9 2 2z"/></svg>
    </li>
    <li>612 550 0193
      <svg viewBox="0 0 16 16" aria-hidden="true"><path d="M4.5 0h7a1 1 0 011 1v14a1 1 0 01-1 1h-7a1 1 0 01-1-1V1a1 1 0 011-1zm.5 2v10h6V2zm3 11a1 1 0 100 2 1 1 0 000-2z"/></svg>
    </li>
    <li>612 550 0175
      <svg viewBox="0 0 16 16" aria-hidden="true"><path d="M4 1h8v4H4zM1 6h14v6h-2.5v3h-9v-3H1zm4.5 4v3.5h5V10z"/></svg>
    </li>
    <li>daniel@tarvex-up.com
      <svg viewBox="0 0 16 16" aria-hidden="true"><path d="M1 4h14v1L8 9.5 1 5zm0 2.5l7 4.5 7-4.5V13H1z"/></svg>
    </li>
    <li>www.tarvex-up.com
      <svg viewBox="0 0 16 16" aria-hidden="true"><circle cx="8" cy="8" r="7"/><path d="M4 5c2 0 2 2 4 2s1 3 0 4-1 3-2 3M10 2c0 2 2 2 3 3" stroke="#f7f7f7" stroke-width="1.3" fill="none"/></svg>
    </li>
  </ul>
</section>

</body>
</html>
```